Stationery Design Project

We need a stationery design for our Norwegian trucking company. We have existed for about 15 years and our 12 drivers uses relatively new vehicles to transport goods around in northern Norway. Long distance routes with fresh fish og food transport is our main operations.

We have already made alogo that's printed on our trucks. The logo and a picture of our trucks is attached. I think the logo i crappy, but since its already in use, changing it is not an option in this round. Still using a better colour scheme in the overall stationery and more interesting fonts is possible (altso in the logo).

Company details:
Name: Kjelvraket AS
Organisation nr 873 615 309
Post adress: 8642 Raudvik

I like minimalism and simplicity. I am avalibly for questions in normal GMT working hours either here or on mail: ivar@fjordlast.no

Reason: Hi. Im extending the deadline because I needed some time to find a vector file of our logo. Sorry for the inconvenience

Hi, and thanks for all your interest in the project. Some updates:

-          I have decided to commit to using one of the designs. Some designer will get the payment.

-          I have extended the deadline with 24 hours since I needed some time to find our firms vector logo (a slow Swedish man was holding me up)

-          We will not choose a design before the deadline. No need to rush.

-          We have received a lot of great design and think there is a need to specified the product we want to make:

o   Business Card for all our employers. I just need the design and will duplicate with the correct numbers and name myself. The information on should be: Logo, employer’s name, Phone number, email, website, Postal number and address. Use this as a template: logo, Leif Brattvoll, 47382066, Leif@fjordlast.no,, fjordlast.no, 8642 Raudvik. The order and placement of the information is your creative decision.

o   Stickers to put on the goods we travel. On the sticker the should be the following information: Logo, phone number, Tekst and link: Fraktæ av Kjelvraket. Ke du syns? Fjordlast.no/tilbakemelding (this means: Handled by Kjelvraket. What do you think Fjordlast.no/feedback -à the link will be a feedback form). The placement the information and size is your creative decision with some stings: we have been thinking of using Drukko for printing and see that a size about 6x6 cm, 8x5 or something like that. (with 3000 copies our budget is 200 punds). Any suggestions of other suppliers are welcome. Drukko price calculator http://www.drukkolabelhouse.co.uk/digital-litho-printing/printing-labels-tags/stickers/

o   Letterhead with logo, address, phone number and organizational number.

o   Envelopes with logo,address, phone number and organizational number.

Have a nice day.

 

 

• Using the blue colour in the logo and using a similar graphic approch.

```html
<!DOCTYPE html>
<html lang="no">
<head>
<meta charset="utf-8">
<title>Kjelvraket AS – Stationery</title>
<link rel="stylesheet" href="https://fonts.googleapis.com/css2?family=Arimo:wght@400;700&family=Roboto+Condensed:wght@700&display=swap">
<style>
  :root {
    --stage: #2b2b2d;
    --paper: #ffffff;
    --brand-blue: #2b3a9e;
    --brand-blue-deep: #22308a;
    --brand-sky: #1c8bd6;
    --accent-orange: #f58220;
    --ink: #2a2a2a;
    --ink-soft: #6a6a6a;
    --silver: #b9bcc0;
    --silver-light: #e3e5e8;
    --truck-grey: #a9abad;
  }
  * { box-sizing: border-box; margin: 0; padding: 0; }
  html, body { width: 1200px; height: 900px; overflow: hidden; }
  body { background: var(--stage); font-family: "Arimo", Arial, sans-serif; color: var(--ink); position: relative; }

  .wordmark { font-family: "Arimo", Arial, sans-serif; font-weight: 700; color: var(--brand-blue); line-height: 1; letter-spacing: -0.3px; }
  .wordmark-site { font-size: 8px; font-weight: 700; color: var(--brand-blue); margin-top: 2px; }
  .waves { position: absolute; left: 0; bottom: 0; width: 100%; display: block; }
  .truck-art { position: absolute; display: block; }

  /* Letterhead */
  .letterhead { position: absolute; left: 45px; top: 148px; width: 425px; height: 600px; background: var(--paper); overflow: hidden; }
  .letterhead .truck-art { left: 0; top: 24px; width: 60px; height: 46px; background: var(--brand-blue); }
  .letterhead .brand { position: absolute; left: 275px; top: 22px; text-align: center; }
  .letterhead .brand .wordmark { font-size: 22px; }
  .letterhead .company { position: absolute; left: 300px; top: 68px; font-size: 8.5px; line-height: 1.35; }
  .letterhead .company strong { font-size: 12px; display: block; margin-bottom: 2px; }
  .letter-body { position: absolute; left: 30px; top: 150px; width: 370px; font-size: 6.4px; line-height: 1.55; color: var(--ink-soft); text-align: justify; }
  .letter-body p { margin-bottom: 9px; }

  /* Business card */
  .business-card { position: absolute; left: 318px; top: 255px; width: 305px; height: 178px; background: var(--paper); overflow: hidden; box-shadow: 0 2px 6px rgba(0,0,0,.45); }
  .business-card .holder { position: absolute; left: 14px; top: 44px; font-family: "Roboto Condensed", Arial, sans-serif; font-size: 10px; line-height: 1.2; text-transform: uppercase; }
  .business-card .holder span { display: block; text-transform: none; font-size: 10px; }
  .business-card .truck-art { left: 14px; top: 72px; width: 100px; height: 66px; background: var(--silver-light); }
  .business-card .brand { position: absolute; left: 170px; top: 22px; text-align: center; }
  .business-card .brand .wordmark { font-size: 20px; }
  .business-card .details { position: absolute; left: 180px; top: 78px; font-size: 8px; line-height: 1.3; }
  .business-card .details strong { font-weight: 400; font-size: 9.5px; display: block; }

  /* Sticker */
  .sticker { position: absolute; left: 473px; top: 487px; width: 150px; height: 180px; background: var(--silver); clip-path: polygon(12% 0, 88% 0, 100% 10%, 100% 90%, 88% 100%, 12% 100%, 0 90%, 0 10%); }
  .sticker-face { position: absolute; inset: 4px; background: var(--paper); clip-path: polygon(12% 0, 88% 0, 100% 10%, 100% 90%, 88% 100%, 12% 100%, 0 90%, 0 10%); overflow: hidden; }
  .sticker .brand { position: absolute; left: 0; right: 0; top: 20px; text-align: center; }
  .sticker .brand .wordmark { font-size: 17px; }
  .sticker .details { position: absolute; left: 0; right: 0; top: 64px; text-align: center; font-size: 8px; line-height: 1.35; }
  .sticker .details strong { display: block; font-size: 10px; color: var(--brand-blue); }

  /* Envelope back */
  .envelope-back { position: absolute; left: 643px; top: 180px; width: 510px; height: 242px; background: var(--paper); overflow: hidden; }
  .envelope-back .flap { position: absolute; left: 0; top: 0; width: 100%; height: 100px; }
  .seal { position: absolute; left: 205px; top: 22px; width: 100px; height: 64px; background: linear-gradient(180deg, var(--silver-light), var(--silver)); clip-path: polygon(0 12%, 50% 0, 100% 12%, 100% 100%, 0 100%); display: flex; flex-direction: column; align-items: center; justify-content: center; }
  .seal .wordmark { font-size: 13px; }
  .seal .wordmark-site { font-size: 6px; }

  /* Envelope front */
  .envelope-front { position: absolute; left: 643px; top: 443px; width: 510px; height: 242px; background: var(--paper); overflow: hidden; }
  .envelope-front .truck-art { left: 0; top: 16px; width: 78px; height: 62px; background: var(--truck-grey); }
  .envelope-front .brand { position: absolute; left: 336px; top: 24px; text-align: center; }
  .envelope-front .brand .wordmark { font-size: 22px; }
  .address-label { position: absolute; left: 30px; top: 148px; width: 98px; height: 94px; background: linear-gradient(180deg, var(--silver-light), var(--silver)); clip-path: polygon(0 10%, 80% 10%, 100% 0, 100% 100%, 0 100%); padding: 18px 6px 0 7px; font-size: 7px; line-height: 1.45; }
  .address-label strong { display: block; font-size: 8.5px; }
</style>
</head>
<body>

<svg width="0" height="0" style="position:absolute" aria-hidden="true">
  <defs>
    <linearGradient id="band-fill" x1="0" y1="0" x2="1" y2="0">
      <stop offset="0" stop-color="#2b3a9e"/>
      <stop offset="0.6" stop-color="#2747b0"/>
      <stop offset="1" stop-color="#1c8bd6"/>
    </linearGradient>
  </defs>
</svg>

<!-- Letterhead -->
<section class="letterhead">
  <div class="truck-art" role="img" aria-label="Truck silhouette illustration"></div>
  <div class="brand">
    <div class="wordmark">Kjelvraket</div>
    <div class="wordmark-site">fjordlast.no</div>
  </div>
  <div class="company">
    <strong>Kjelvraket AS</strong>
    Organisation nr 873 615 309<br>
    Post adress: 8642 Raudvik
  </div>
  <div class="letter-body">
    <p>We carry fresh fish and chilled food along the long roads of northern Norway. Our drivers know every route, every ferry and every winter pass, and they deliver on time through dark months and bright summer nights alike.</p>
    <p>This letter confirms the details we discussed about your transport needs. Please review the schedule, the pickup points and the agreed rates below, and let us know if anything should be adjusted before the first delivery leaves the terminal.</p>
    <p>All cargo is handled in temperature controlled trailers and tracked from loading to arrival.</p>
    <p>We look forward to working with you. Should you have questions about routes, capacity or documentation, our office is ready to help during normal working hours, and a driver can always be reached while on the road with your goods.</p>
  </div>
  <svg class="waves" viewBox="0 0 425 160" height="160" preserveAspectRatio="none" aria-hidden="true">
    <path d="M0,18 C130,95 300,98 425,46 L425,160 L0,160 Z" fill="url(#band-fill)"/>
    <path d="M0,12 C130,88 300,92 425,38" fill="none" stroke="#ffffff" stroke-width="8"/>
    <path d="M0,2 C130,76 300,80 425,26" fill="none" stroke="#f58220" stroke-width="8"/>
  </svg>
</section>

<!-- Business card -->
<section class="business-card">
  <div class="holder">Leif Brattvoll<span>47382066</span></div>
  <div class="truck-art" role="img" aria-label="Faint truck cab illustration"></div>
  <div class="brand">
    <div class="wordmark">Kjelvraket</div>
    <div class="wordmark-site">fjordlast.no</div>
  </div>
  <div class="details">
    <strong>Kjelvraket AS</strong>
    Organisation nr 873 615 309<br>
    Post adress: 8642 Raudvik<br>
    Leif@fjordlast.no
  </div>
  <svg class="waves" viewBox="0 0 305 60" height="60" preserveAspectRatio="none" aria-hidden="true">
    <path d="M0,40 C90,62 220,40 305,0 L305,60 L0,60 Z" fill="url(#band-fill)"/>
    <path d="M0,34 C90,56 220,34 305,-6" fill="none" stroke="#ffffff" stroke-width="4"/>
    <path d="M0,28 C90,50 220,28 305,-12" fill="none" stroke="#f58220" stroke-width="4"/>
  </svg>
</section>

<!-- Sticker -->
<section class="sticker">
  <div class="sticker-face">
    <svg class="waves" viewBox="0 0 142 80" height="80" preserveAspectRatio="none" aria-hidden="true">
      <path d="M0,0 C20,50 70,72 142,70 L142,80 L0,80 Z" fill="url(#band-fill)"/>
      <path d="M10,0 C28,44 74,62 142,60" fill="none" stroke="#f58220" stroke-width="3"/>
    </svg>
    <div class="brand">
      <div class="wordmark">Kjelvraket</div>
      <div class="wordmark-site">fjordlast.no</div>
    </div>
    <div class="details">
      <strong>Kjelvraket AS</strong>
      Organisation nr 873 615 309<br>
      Post adress: 8642 Raudvik<br>
      Leif@fjordlast.no
    </div>
  </div>
</section>

<!-- Envelope back -->
<section class="envelope-back">
  <svg class="flap" viewBox="0 0 510 100" preserveAspectRatio="none" aria-hidden="true">
    <path d="M0,0 L510,0 L510,8 C470,40 380,60 255,86 C130,60 40,40 0,8 Z" fill="url(#band-fill)"/>
    <path d="M8,14 C50,40 140,58 255,80 C370,58 460,40 502,14 L502,8 C460,34 370,52 255,74 C140,52 50,34 8,8 Z" fill="#ffffff" opacity="0.9"/>
  </svg>
  <div class="seal">
    <div class="wordmark">Kjelvraket</div>
    <div class="wordmark-site">fjordlast.no</div>
  </div>
</section>

<!-- Envelope front -->
<section class="envelope-front">
  <div class="truck-art" role="img" aria-label="Grey truck illustration"></div>
  <div class="brand">
    <div class="wordmark">Kjelvraket</div>
    <div class="wordmark-site">fjordlast.no</div>
  </div>
  <svg class="waves" viewBox="0 0 510 150" height="150" preserveAspectRatio="none" aria-hidden="true">
    <path d="M0,20 C120,100 300,150 510,118 L510,150 L0,150 Z" fill="url(#band-fill)"/>
    <path d="M0,12 C130,90 300,138 510,108" fill="none" stroke="#ffffff" stroke-width="6"/>
    <path d="M0,2 C140,80 300,126 510,96" fill="none" stroke="#f58220" stroke-width="6"/>
  </svg>
  <div class="address-label">
    <strong>Kjelvraket AS</strong>
    Organisation nr 873 615 309<br>
    Post adress: 8642 Raudvik<br>
    Leif@fjordlast.no
  </div>
</section>

</body>
</html>
```